Book Cover Design — Literary Memoir — Each Summer the Orchard Forgot Its Keys

I need a professional book cover design for a literary memoir titled Each Summer the Orchard Forgot Its Keys by Corinne T. Hadley. This project requires two complete cover files — one for the paperback edition and one for the hardcover edition — both built to Plinthpress print specifications.
The author photograph is attached and is the centerpiece of the front cover. It is not a placeholder. The front cover contains three elements only: the author name, the photograph, and the title. No subtitle, no taglines, no additional elements.
A complete creative brief is attached. Read it in full before submitting a design. It contains all specifications, typography direction, mood references, comparable covers, and file delivery requirements.
A back cover text package is also attached for layout reference. A Canva reference design showing the directional concept is attached — the photograph placement and title position are correct. The typography needs professional resolution.
This is a literary memoir in the tradition of Unfolded, Tideworks, and The Copper Meadow. The cover must feel sophisticated, restrained, and literary — not self-help, not inspirational, not decorative.
Two formats required. Paperback and hardcover. Plinthpress spine templates for both formats are attached.
Full file delivery specifications are in the brief. The color photograph in front of the water in the blue jacket should be used inside the dust jacket with the bio if a dust jacket edition is produced.
Do not use literal interpretations of the title. No whiskey glasses, no alcohol, no angel figurines, no cherubs, no wings, no halos, no religious imagery of any kind. The title is metaphorical. The cover must not illustrate it literally.
The author photograph is the only image on the front cover. Typography, photograph, author name. Nothing else.

BRIEF UPDATE — BACK COVER PHOTOGRAPH AND LAYOUT
Please read before submitting.
A second author photograph is attached to this brief. It is a color photograph and it is specifically for the back cover author bio section only. Do not convert it to black and white. Do not use it on the front cover. The front cover uses only the black and white photograph already provided. The color photograph is for the back cover exclusively. Do not generate, substitute, or alter the image. Use only the file provided.
Back cover layout — exact order top to bottom:
1. Endorsement quotes — top of back cover.
Three endorsement quote placeholders, each approximately two to three lines of quote text followed by the endorser name and credential on the line below. Separate each quote with a thin rule or line. Set in italics, smaller than the jacket copy text. These are placeholders — final quotes are pending.
2. Jacket copy — middle of back cover.
The main descriptive text block. Set in a clean readable serif, slightly larger than the endorsement quotes. Preserve all paragraph breaks exactly as written. Two pull quotes inside the jacket copy must be set in gold, framed by thin gold rules above and below, matching the gold accent color used for ITS KEYS on the front cover. Use the following final approved text exactly as written:
At forty-three, she stood in a villa in Abu Dhabi at four in the morning and understood that the marriage was over, the career she had given up was not coming back, and the country she was standing in was not hers. She had two boys to raise, a spousal visa, and no plan.
She came by the next move honestly.
A great-grandmother who crossed the Atlantic alone in 1907 and built a life from nothing. A grandmother on the other side, told by an anonymous letter that the blood in her veins was tainted, who answered the letter with the rest of her life. A guardian angel with a slightly crooked halo and a highball in her hand. Four generations of women who refused the smaller life and passed something down that none of them named and none of them had to.
Each Summer the Orchard Forgot Its Keys is the story of what happens when a woman finally stops building someone else's life and starts building her own.
[GOLD PULL QUOTE — framed by thin gold rules above and below, set in gold, centered:]
For anyone who has ever had no choice but to start over — and for anyone still waiting for the courage to.
[End gold pull quote]
Proof that someone has navigated it.
And that you can too.
The closing two lines — Proof that someone has navigated it. and And that you can too. — should each sit on their own line with breathing room around them. They are the closing beats of the back cover.
3. Author bio with photograph — bottom of back cover.
Place the color author photograph on the left side, cropped to approximately a two inch square or whatever proportion fits the layout cleanly. The author bio text runs to the right of the photograph. The author name CORINNE T. HADLEY should appear above the bio text in gold caps. Use the following text exactly as written, with one paragraph break inserted between finally behind her. and When the marriage ended:
Corinne T. Hadley is the founder and CEO of Tallow Meridian, an international advisory firm operating across the United States, the Middle East, Africa, and Europe. She gave up a rising career in Pennsylvania state government to support her husband, an KR-19C Marlin pilot, through five combat deployments. She followed him to Abu Dhabi in 2013 believing the hardest years were finally behind her.
When the marriage ended, she was forty-three, in a country that was not hers, with no job and no road back. She rebuilt from nothing and went on to advise governments, ministries, Vantor 300 companies, and members of the Royal Family of Abu Dhabi. She has spoken on stages in over thirty countries. She lives in North Carolina.
4. Barcode and ISBN — lower right corner.
Minimum clear space 2 inches wide by 1.2 inches tall. No other design elements within 0.25 inches of the barcode block.
Background treatment:
The back cover background should not be flat black. Add a subtle texture, very light gradient, or carry a soft element from the front cover photograph into the background to give the back cover visual depth and weight. It should feel finished and intentional, not like an empty void with text dropped onto it.
Typography:
Consistent with the front cover type treatment. Same font family throughout. Endorsement quotes in italics. Jacket copy in roman. Author bio in roman at slightly smaller size than the jacket copy. The gold pull quote inside the jacket copy is set in gold, centered, framed by thin gold rules above and below. The author name above the bio is set in gold caps. All other text is white or very light grey, fully legible against the dark background.
Do not add anything else to the back cover. No additional images, no decorative elements, no additional text beyond what is specified above.

Target Market(s)

Women aged 35 to 65. Readers of literary memoir and narrative nonfiction. Military spouse community. Women navigating reinvention, divorce, or major life transition. Business and leadership audience. Book club readers. Comparable readership to Unfolded by Mirela Oakhurst, Tideworks by Lina Vastoff, and The Copper Meadow by Rosalind Fenwick.

Industry/Entity Type

Industry: Book publishing. Literary memoir. Narrative nonfiction.

Font styles to use
Serif
Sans Serif
Other font styles liked:
• Garamond, Caslon, or Freight Display. Clean geometric sans-serif such as Futura or Gotham. Avoid fonts that read as corporate, casual, or decorative. The font chosen for the title must work in both white and gold without losing legibility against the dark photographic background.

Requirements
Must have
• The author photograph — black and white, attached, full bleed, centerpiece of the cover. This is not a placeholder. Do not alter, colorize, or filter it. Author name: CORINNE T. HADLEY — top of cover, white, clean and strong. Title: EACH SUMMER THE ORCHARD FORGOT ITS KEYS — lower third of cover. ITS KEYS in gold. All other title words in white. Unified typography — all words of the title must feel like one visual system. This is the primary design challenge. Two complete cover files — one paperback, one hardcover — built to the attached Plinthpress spine templates. Print-ready PDF both formats, editable source files both formats, front cover flat image for ebook, square audiobook cover 2400 x 2400 pixels.
Nice to have
• A drop cap treatment on the I that opens the title, if the designer can make it feel intentional and unified with the rest of the title rather than decorative. Back cover placeholder showing the design treatment and barcode placement area — full back cover text is provided in the attached back cover package for layout sizing. Subtle gold accent elements if they enhance rather than decorate — the gold should feel intentional, not ornamental.
Should not have
• No subtitle. No tagline. No credential lines. No award badges. No endorsement quotes on the front cover. No brushstroke fonts. No handwritten fonts. No decorative display fonts. No more than two typeface families in the entire design. No additional colors beyond white, gold, and the black and white photograph. No colorizing, filtering, or altering the photograph in any way. No graphic elements, borders, frames, or decorative embellishments. No busy or cluttered layout — negative space is the design language of this cover. Nothing that reads as self-help, inspirational poster, or business book. Do not use literal interpretations of the title. No whiskey glasses, no alcohol, no angel figurines, no cherubs, no wings, no halos, no religious imagery of any kind. The title is metaphorical. The cover must not illustrate it literally. The author photograph is the only image on the front cover. Typography, photograph, author name. Nothing else.

```html
<!DOCTYPE html>
<html lang="en">
<head>
<meta charset="utf-8">
<title>Each Summer the Orchard Forgot Its Keys — Cover Spread</title>
<link rel="stylesheet" href="https://fonts.googleapis.com/css2?family=Bodoni+Moda:wght@400;500&family=Tinos:ital@0;1&family=Montserrat:wght@400;600&display=swap">
<style>
  :root {
    --stage: #565656;
    --back-top: #202020;
    --back-bottom: #121212;
    --spine: #171717;
    --white: #f4f4f2;
    --light: #d9d9d6;
    --gold: #c29a4a;
    --gold-bright: #d8b56a;
    --gold-deep: #9c7632;
    --photo-dark: #0e0e0e;
    --photo-mid: #3a3a3a;
    --photo-light: #8a8a8a;
  }
  * { box-sizing: border-box; margin: 0; padding: 0; }
  html, body { width: 1200px; height: 960px; overflow: hidden; }
  body { background: var(--stage); position: relative; }

  .cover-spread {
    position: absolute; left: 40px; top: 86px;
    width: 1120px; height: 788px;
    display: flex;
  }

  /* Back cover */
  .back-cover {
    position: relative; width: 517px; height: 100%;
    background: radial-gradient(ellipse at 70% 30%, #2a2a2a 0%, transparent 60%),
                linear-gradient(180deg, var(--back-top), var(--back-bottom));
    color: var(--light);
    font-family: "Tinos", "Times New Roman", serif;
  }
  .endorsements { position: absolute; left: 60px; width: 410px; top: 40px; text-align: center; }
  .endorsement { font-size: 8.4px; line-height: 11.5px; letter-spacing: 0.09em; margin-bottom: 9px; }
  .endorsement span { display: block; }

  .gold-rule { position: absolute; height: 1px; background: var(--gold); }
  .gold-rule .mark {
    position: absolute; left: 50%; top: -3px; width: 6px; height: 6px;
    background: var(--gold); transform: translateX(-50%) rotate(45deg);
  }
  .back-rule-top { left: 135px; width: 260px; top: 175px; }
  .back-rule-bio { left: 60px; width: 405px; top: 494px; }

  .jacket-copy {
    position: absolute; left: 60px; top: 186px; width: 410px;
    font-size: 10.6px; line-height: 13.3px; text-align: justify;
  }
  .jacket-copy p { margin-bottom: 13px; }
  .jacket-copy .opener { color: var(--gold); margin-bottom: 7px; }
  .jacket-copy .beat { text-align: left; }

  .author-bio { position: absolute; left: 59px; top: 507px; width: 405px; display: flex; gap: 7px; }
  .bio-photo {
    flex: none; width: 94px; height: 128px;
    background: linear-gradient(160deg, #b9c6d2 0%, #c9a880 40%, #1d2a44 80%, #f0f0f0 100%);
  }
  .bio-name {
    font-family: "Montserrat", Arial, sans-serif; font-weight: 600;
    color: var(--gold); font-size: 10.5px; letter-spacing: 0.16em; margin-bottom: 2px;
  }
  .bio-text { font-size: 8.2px; line-height: 11.7px; text-align: justify; color: var(--light); }

  .barcode-space {
    position: absolute; left: 306px; top: 655px; width: 164px; height: 95px;
    background: #dcdcdc;
  }

  /* Spine */
  .spine {
    position: relative; width: 86px; height: 100%;
    background: linear-gradient(90deg, #101010, var(--spine) 40%, #1c1c1c 70%, #0f0f0f);
  }
  .spine-title {
    position: absolute; left: 50%; top: 58px; transform: translateX(-50%);
    writing-mode: vertical-rl;
    font-family: "Bodoni Moda", "Didot", serif; font-size: 18px; letter-spacing: 0.01em;
    color: var(--white); white-space: nowrap;
  }
  .spine-title .initial { font-size: 25px; }
  .spine-title .accent { color: var(--gold); }
  .spine-rule { left: 13px; width: 60px; }
  .spine-rule-1 { top: 567px; }
  .spine-rule-2 { top: 729px; }
  .spine-author {
    position: absolute; left: 50%; top: 578px; transform: translateX(-50%);
    writing-mode: vertical-rl;
    font-family: "Montserrat", Arial, sans-serif; font-size: 12px; letter-spacing: 0.06em;
    color: var(--white); white-space: nowrap;
  }

  /* Front cover */
  .front-cover { position: relative; width: 517px; height: 100%; overflow: hidden; }
  .front-photo {
    position: absolute; inset: 0;
    background:
      radial-gradient(ellipse 45% 42% at 88% 44%, var(--photo-light) 0%, #5a5a5a 35%, transparent 75%),
      radial-gradient(ellipse 55% 50% at 40% 45%, var(--photo-mid) 0%, transparent 70%),
      linear-gradient(180deg, #1a1a1a 0%, var(--photo-dark) 100%);
  }
  .front-author {
    position: absolute; left: 42px; top: 34px;
    font-family: "Bodoni Moda", "Didot", serif; font-size: 28px; font-weight: 400;
    letter-spacing: 0.17em; color: var(--white); white-space: nowrap;
  }
  .front-title {
    position: absolute; left: 24px; top: 448px;
    font-family: "Bodoni Moda", "Didot", serif; font-weight: 400; color: var(--white); line-height: 1;
  }
  .title-line-1 { display: flex; align-items: flex-end; gap: 6px; }
  .drop-cap { font-size: 82px; line-height: 0.78; }
  .title-line-1 .rest { font-size: 31px; letter-spacing: 0.09em; padding-bottom: 2px; }
  .title-line-2 { display: block; font-size: 28px; letter-spacing: 0.05em; margin-top: 14px; white-space: nowrap; }
  .title-line-3 {
    display: inline-block; font-size: 86px; letter-spacing: 0; margin-top: 4px; white-space: nowrap;
    color: var(--gold);
    background: linear-gradient(180deg, var(--gold-bright), var(--gold) 55%, var(--gold-deep));
    -webkit-background-clip: text; background-clip: text; -webkit-text-fill-color: transparent;
  }
  .front-rule { left: 24px; width: 404px; top: 681px; }
</style>
</head>
<body>
<div class="cover-spread">

  <section class="back-cover">
    <div class="endorsements">
      <p class="endorsement"><span>ENDORSEMENT QUOTE ONE</span><span>approximately 2 to 3 lines of quote text here, followed by attribution on the line below.</span><span>Endorser Name, Title or Credential</span></p>
      <p class="endorsement"><span>ENDORSEMENT QUOTE ONE</span><span>approximately 2 to 3 lines of quote text here, followed by attribution on the line below.</span><span>Endorser Name, Title or Credential</span></p>
      <p class="endorsement"><span>ENDORSEMENT QUOTE ONE</span><span>approximately 2 to 3 lines of quote text here, followed by attribution on the line below.</span><span>Endorser Name, Title or Credential</span></p>
    </div>
    <div class="gold-rule back-rule-top"><span class="mark"></span></div>

    <div class="jacket-copy">
      <p class="opener">It begins before she is born.</p>
      <p>In 1907, Ilka Varosne crosses the Atlantic alone at twenty-five, leaving behind an illegitimate son, a forbidden love affair, and a family that has made clear she is no longer welcome. She builds a life from nothing in Pittsburgh, keeps a secret for decades, and passes something down to the women who follow her that she never names and never has to. The refusal to accept a smaller life than the one you are capable of building. It travels through the blood.</p>
      <p>Four generations later, her great-granddaughter arrives in Abu Dhabi at forty-three to find a marriage unexpectedly unraveling, a career long-abandoned to support her husband's, two boys to raise, and no plan. What she does next — a quilt guild, a palace, ministerial meetings across Africa, stages in thirty-one countries, and a global company built from nothing — is what happens when a woman finally stops building someone else's life and starts building her own.</p>
      <p>Each Summer the Orchard Forgot Its Keys is the story of four generations of women who refused the smaller life.</p>
      <p class="beat">This is a book for anyone who has ever been too much for the life they were given — and who refused to stay in it.</p>
      <p class="beat">Proof that someone has navigated it.</p>
      <p class="beat">And that you can too.</p>
    </div>

    <div class="gold-rule back-rule-bio"></div>

    <div class="author-bio">
      <div class="bio-photo" role="img" aria-label="Colour author photograph of Corinne T. Hadley in a blue jacket in front of water"></div>
      <div class="bio-body">
        <h2 class="bio-name">CORINNE T. HADLEY</h2>
        <p class="bio-text">Corinne T. Hadley is the founder and CEO of Tallow Meridian, a specialized global advisory firm operating across five continents. She gave up a rising career in government service to support her husband, an KR-19C Marlin pilot through four combat deployments, and followed him to Abu Dhabi believing the hardest years were finally behind her. When the marriage unraveled, she was forty-three, in a country that was not hers, with no job and no road back. She built her professional career from scratch in Abu Dhabi following the reinvention at the center of this book. She has spoken at official Concord Nations side events and on stages in thirty-one countries, and her work has been featured in the Harbor Ledger Journal, Nation Daily, and Capital Steward. She lives in North Carolina.</p>
      </div>
    </div>

    <div class="barcode-space" aria-label="Barcode and ISBN area"></div>
  </section>

  <section class="spine">
    <div class="spine-title"><span class="initial">E</span>ACH SUMMER THE ORCHARD FORGOT <span class="accent">ITS KEYS</span></div>
    <div class="gold-rule spine-rule spine-rule-1"><span class="mark"></span></div>
    <div class="spine-author">CORINNE T. HADLEY</div>
    <div class="gold-rule spine-rule spine-rule-2"><span class="mark"></span></div>
  </section>

  <section class="front-cover">
    <div class="front-photo" role="img" aria-label="Black and white author portrait of Corinne T. Hadley, half her face at the right edge against a dark background"></div>
    <h2 class="front-author">CORINNE T. HADLEY</h2>
    <h1 class="front-title">
      <span class="title-line-1"><span class="drop-cap">E</span><span class="rest">ACH SUMMER</span></span>
      <span class="title-line-2">THE ORCHARD FORGOT</span>
      <span class="title-line-3">ITS KEYS</span>
    </h1>
    <div class="gold-rule front-rule"><span class="mark"></span></div>
  </section>

</div>
</body>
</html>
```